Business card for Crestline Bathrooms

Please design a business card for our bathroom renovation business. You can use my existing logo, but if you have an idea to modernize it, I would like to see it. Please see attached files first. I would like to use the blue and the orange theme. I like the concept of using the shower head in the logo. Please find following a design (or two) that I have been trying to create with my limited resources. That design was for a sign, but I was going to adopt it and use it as a business card as well. I like the concept of the water splash but I don’t think it “flows” nicely together with the logo. Another thought is that maybe creating the logo out of water splash could work and have a dramatic effect (like the water text and the butterfly picture attached with similar background instead of white). If the above doesn’t work I would like to see a modern simplified design. One of the attached files named as the unwanted business card has all the details that I want included in the business card. Please note that it is two sided.
Updates

I am very thankful for the designs that I have received, but they are very similar and only a couple of attempts to do something with the water splash as per my original brief. Modernizing the logo and having it made out of out of water splash with the orange as color accent could work and have a dramatic effect (like the water text and the butterfly picture attached with similar background instead of white). Please do not use the butterfly itself! This is just an example that images can be created out of water splash.

Contact Information for Business Card

all the details are on the unwonted business card file included

Colors
3176b5

Requirements
Nice to have
• Copied from the brief:
• ... maybe creating the logo out of water splash could work and have a dramatic effect (like the water text and the butterfly picture attached with similar background instead of white). Please do not use the butterfly itself!
Should not have
• I am getting designs with a butterfly. The butterfly picture was an example of creating something from a water splash. The butterfly itself has no association with anything other than the concept of creating a logo out of water splash. Sorry, I thought I was clear in the brief.

```html
<!DOCTYPE html>
<html lang="en">
<head>
<meta charset="utf-8">
<title>Crestline Bathrooms – Business Card</title>
<link rel="stylesheet" href="https://fonts.googleapis.com/css2?family=Delius&family=Roboto:wght@400;500&display=swap">
<style>
  :root {
    --navy: #023f6b;
    --coral: #e9786b;
    --card: #f4f4f3;
    --backdrop: #e6e6e6;
    --ink: #ffffff;
    --grey-text: #4d4d4d;
    --badge: #4a4a4a;
  }
  * { box-sizing: border-box; margin: 0; padding: 0; }
  html, body { width: 1200px; height: 960px; overflow: hidden; }
  body { background: var(--backdrop); position: relative; font-family: "Roboto", Arial, sans-serif; }

  .card {
    position: absolute; width: 600px; height: 342px;
    background: var(--card); overflow: hidden;
    box-shadow: 0 2px 4px rgba(0,0,0,.25);
  }
  .card--front { left: 314px; top: 113px; }
  .card--back  { left: 311px; top: 472px; }

  .wave { position: absolute; inset: 0; width: 600px; height: 342px; }

  .brand {
    position: absolute; color: var(--navy); font-family: "Roboto", Arial, sans-serif;
    font-weight: 500; display: flex; align-items: center; gap: 10px;
  }
  .brand__dot { width: 14px; height: 14px; border-radius: 50%; background: var(--coral); flex: none; }
  .brand--front { left: 60px; top: 92px; font-size: 26px; line-height: 1.05; }
  .brand--back  { left: 40px; top: 96px; font-size: 54px; line-height: 1.05; }
  .brand--back .brand__dot { width: 30px; height: 30px; }

  .holder-name {
    position: absolute; right: 36px; top: 40px;
    font-family: "Delius", "Comic Sans MS", cursive; font-size: 25px; font-weight: 400; color: var(--navy);
    letter-spacing: .5px;
  }

  .contact { position: absolute; right: 36px; top: 190px; color: var(--ink); font-size: 14px; list-style: none; }
  .contact__item { display: flex; justify-content: flex-end; align-items: center; gap: 10px; line-height: 19px; }
  .contact__item--gap { margin-top: 9px; }
  .contact__text { text-align: right; white-space: nowrap; }
  .contact__icon { width: 14px; height: 14px; flex: none; }
  .contact__icon--blank { visibility: hidden; }

  .badges { position: absolute; left: 384px; top: 192px; display: flex; align-items: center; gap: 16px; }
  .badge--round { width: 30px; height: 34px; border-radius: 6px; background: var(--badge); }
  .badge__divider { width: 1px; height: 34px; background: var(--badge); }
  .badge--wide { width: 118px; height: 28px; background: var(--badge); }

  .services { position: absolute; right: 32px; top: 243px; list-style: none; color: var(--grey-text); font-size: 14.5px; }
  .services__item { display: flex; justify-content: flex-end; align-items: center; gap: 7px; line-height: 19px; white-space: nowrap; }
  .services__item::after { content: ""; width: 5px; height: 5px; border-radius: 50%; background: var(--navy); }
</style>
</head>
<body>

<section class="card card--front" aria-label="Card front">
  <svg class="wave" viewBox="0 0 600 342" aria-hidden="true">
    <path class="wave__coral" fill="var(--coral)" d="M25,222 C80,290 150,312 230,292 C300,270 390,100 515,98 C565,94 590,135 600,172 L600,342 L0,342 L0,222 Z"/>
    <path class="wave__rule" fill="#ffffff" d="M25,226 C80,296 150,318 232,298 C305,278 395,116 517,112 C563,110 588,152 600,186 L600,342 L0,342 L0,226 Z"/>
    <path class="wave__base" fill="var(--navy)" d="M25,229 C80,300 150,322 234,302 C308,282 398,122 519,118 C561,117 586,158 600,192 L600,342 L0,342 L0,229 Z"/>
    <path class="wave__tongue" fill="var(--navy)" d="M0,200 C40,250 130,275 230,258 C140,282 60,262 25,222 L25,342 L0,342 Z"/>
  </svg>

  <div class="brand brand--front"><span class="brand__dot"></span><span>Crestline<br>Bathrooms</span></div>
  <h1 class="holder-name">Daniel Moravec</h1>

  <ul class="contact">
    <li class="contact__item"><span class="contact__text">PO Box 41</span>
      <svg class="contact__icon" viewBox="0 0 14 14"><path fill="var(--coral)" d="M7,1 C4.2,1 2.5,3 2.5,5.3 C2.5,8.5 7,13 7,13 C7,13 11.5,8.5 11.5,5.3 C11.5,3 9.8,1 7,1 Z M7,3.6 A1.7,1.7 0 1 1 7,7 A1.7,1.7 0 1 1 7,3.6 Z"/></svg></li>
    <li class="contact__item"><span class="contact__text">Kelmscott Vale 2715</span>
      <svg class="contact__icon contact__icon--blank" viewBox="0 0 14 14"></svg></li>
    <li class="contact__item contact__item--gap"><span class="contact__text">0412 555 018</span>
      <svg class="contact__icon" viewBox="0 0 14 14"><path fill="var(--coral)" d="M3,1.5 L5,1.5 L6,4.5 L4.6,5.6 C5.3,7.2 6.8,8.7 8.4,9.4 L9.5,8 L12.5,9 L12.5,11 C12.5,12 11.7,12.6 10.8,12.5 C6,12 2,8 1.5,3.2 C1.4,2.3 2,1.5 3,1.5 Z"/></svg></li>
    <li class="contact__item"><span class="contact__text">6200 5512</span>
      <svg class="contact__icon" viewBox="0 0 14 14"><rect x="3.5" y="1" width="7" height="12" rx="1.2" fill="none" stroke="var(--coral)" stroke-width="1.5"/><circle cx="7" cy="11" r=".8" fill="var(--coral)"/></svg></li>
    <li class="contact__item"><span class="contact__text">daniel@crestlinebathrooms.com.au</span>
      <svg class="contact__icon" viewBox="0 0 14 14"><rect x="1.5" y="3" width="11" height="8" fill="var(--coral)"/><path d="M1.5,3 L7,7.5 L12.5,3" fill="none" stroke="var(--navy)" stroke-width="1"/></svg></li>
    <li class="contact__item"><span class="contact__text">crestlinebathrooms.com.au</span>
      <svg class="contact__icon" viewBox="0 0 14 14"><circle cx="7" cy="7" r="5.5" fill="var(--coral)"/><path d="M1.5,7 H12.5 M7,1.5 C4.5,4.5 4.5,9.5 7,12.5 M7,1.5 C9.5,4.5 9.5,9.5 7,12.5" fill="none" stroke="var(--navy)" stroke-width=".8"/></svg></li>
  </ul>
</section>

<section class="card card--back" aria-label="Card back">
  <div class="brand brand--back"><span class="brand__dot"></span><span>Crestline<br>Bathrooms</span></div>

  <div class="badges">
    <span class="badge--round" aria-hidden="true"></span>
    <span class="badge__divider" aria-hidden="true"></span>
    <span class="badge--wide" aria-hidden="true"></span>
  </div>

  <ul class="services">
    <li class="services__item">Complete Bathroom Renovations &amp; Remodelling</li>
    <li class="services__item">Highly Skilled &amp; Qualified Tradespeople</li>
    <li class="services__item">Professional Service From Concept To Completion</li>
    <li class="services__item">All Work Guaranteed</li>
  </ul>
</section>

</body>
</html>
```